Bright Trails, Strong Spirits Poster for American Indian Older Adults

We need am 11" x 17" poster designed for a health outreach project designed to reach older U.S. American Indians. The materials developed through this project will be distributed to American Indian and Alaska Native tribes, communities and tribal-serving organizations across the U.S. (more than 500 different tribes). If we find a successful design we will work with that designer to produce at least one other item we need design work for using the same look/feel and maybe other materials for this project. (more work!). The poster will include a set of facts (bulleted list on the attached document) that we would like presented in an "infographic" style. The design must be reflective of the American Indian culture and designed with older adults (65 and older) in mind. Imagery plays a strong role in the American Indian culture in the U.S. images of the heart, water, feathers, circle of life, etc. If you use photos of people they must include older adults and they must be American Indian (Native American). We prefer deep earth tones for the color scheme. The design must take into account design principles for older adults: 1. Try not to put colored font on colored background 2. Ensure high contrast for text 3. Font style should be sans serif, not cursive,decorative or heavily stylized because it is harder to read 4. Avoid using all caps 5. Don't print sideways or on top of images, shaded, backgrounds, etc. 6. All images should related specifically to the content of the text and be culturally appropriate for both older adults and American Indians. The final design should be easy to read and appeal to older American Indian adults. We need to incorporate three logos on the poster towards the bottom they should not be the center/focus of the poster. We also need to include a statement about who produced the materials- that can be very small below the logos at the bottom of the poster. We've attached the text for the poster and three logo files (note one is solid blue- we will finalize that after the document design is selected but need a placeholder for that logo.

Target Market(s)

Older adult (65 and older) American Indian and Alaska Natives and their family members in tribes, communities and tribal-serving organizations across the US

Font styles to use
Sans Serif

Requirements
Must have
• Must adhere to good design principles for older adults (listed in project description)
• Must feature culturally appropriate/targeted imagery and design look and feel

```html
<!DOCTYPE html>
<html lang="en">
<head>
<meta charset="utf-8">
<title>Bright Trails, Strong Spirits</title>
<link href="https://fonts.googleapis.com/css2?family=Source+Sans+3:ital,wght@0,400;0,600;0,700;1,700&family=PT+Sans+Narrow:wght@400;700&display=swap" rel="stylesheet">
<style>
  :root {
    --rust: #b9512c;
    --rust-deep: #a8441f;
    --rust-soft: #c8653d;
    --orange: #dc7b3b;
    --navy: #2f3a4f;
    --gold: #e0a257;
    --cream: #f6e1cc;
    --sand: #e3aa7a;
    --brown: #4a2917;
    --heart: #c0321f;
    --white: #ffffff;
    --footer: #ffffff;
  }
  * { box-sizing: border-box; margin: 0; padding: 0; }
  html, body { width: 908px; height: 1200px; overflow: hidden; background: var(--rust); }
  body { font-family: "Source Sans 3", sans-serif; color: var(--white); }
  .poster { position: relative; width: 908px; height: 1200px; overflow: hidden; background: var(--rust); }
  .backdrop {
    position: absolute; left: 0; top: 0; width: 908px; height: 1141px;
    background: radial-gradient(ellipse at 30% 55%, var(--rust-soft) 0%, var(--rust) 55%, var(--rust-deep) 100%);
  }
  .title-box {
    position: absolute; left: 23px; top: 29px; width: 730px; height: 219px;
    background: var(--navy); border: 5px solid var(--gold);
  }
  .title {
    position: absolute; left: 45px; top: 66px;
    font-weight: 600; font-size: 68px; line-height: 72px; letter-spacing: -0.5px;
  }
  .portrait {
    position: absolute; left: 518px; top: 20px; width: 390px; height: 452px;
    background: linear-gradient(180deg, #c9714c 0%, #e9d3c4 35%, #f1d9d4 70%, #e7c4bb 100%);
  }
  .heart { position: absolute; left: 564px; top: 226px; width: 292px; height: 244px; }
  .heart svg { position: absolute; inset: 0; }
  .heart-text { position: absolute; inset: 0; color: var(--white); }
  .heart-lead { position: absolute; left: 67px; top: 76px; font-size: 19px; font-weight: 600; }
  .heart-num { position: absolute; left: 70px; top: 88px; font-size: 100px; font-weight: 700; line-height: 1; }
  .heart-sup { position: absolute; left: 133px; top: 96px; font-size: 15px; font-weight: 700; }
  .heart-rest { position: absolute; left: 145px; top: 112px; font-size: 18px; line-height: 18px; }
  .subtitle {
    position: absolute; left: 45px; top: 282px;
    font-weight: 700; font-style: italic; font-size: 31px; line-height: 36px;
  }
  .hatch {
    position: absolute; left: 45px; top: 432px; width: 378px; height: 10px;
    background: repeating-linear-gradient(120deg, rgba(255,255,255,0.55) 0 1px, transparent 1px 5px);
  }
  .risk {
    position: absolute; left: 34px; top: 640px;
    font-size: 20px; line-height: 47px; color: var(--white);
  }
  .pulse { position: absolute; left: 30px; top: 790px; width: 370px; height: 44px; }
  .cta-label {
    position: absolute; left: 36px; top: 958px; width: 338px; height: 50px;
    background: var(--sand); color: var(--brown);
    font-weight: 700; font-size: 22px; line-height: 22px; padding: 3px 8px; letter-spacing: 0.5px;
  }
  .cta-text {
    position: absolute; left: 44px; top: 1016px;
    font-size: 23px; line-height: 24px; color: var(--cream);
  }
  .cta-rule { position: absolute; left: 36px; top: 1070px; width: 342px; height: 3px; background: var(--sand); }
  .border-band {
    position: absolute; left: 0; top: 1119px; width: 462px; height: 22px;
    background: linear-gradient(90deg, #8f3a1f, #c98765, #8f3a1f);
  }
  .facts { position: absolute; left: 464px; top: 472px; width: 444px; height: 669px; background: var(--orange); }
  .map {
    position: absolute; left: 32px; top: 37px; width: 361px; height: 196px;
    background: var(--cream); border-radius: 40px 60px 30px 70px / 30px 40px 80px 50px;
  }
  .stat-big { position: absolute; font-family: "PT Sans Narrow", sans-serif; font-weight: 700; color: var(--brown); line-height: 1; letter-spacing: -2px; }
  .stat-note { position: absolute; font-size: 19px; line-height: 19px; color: var(--white); }
  .millions { left: 65px; top: 96px; font-size: 72px; }
  .millions-unit { position: absolute; left: 163px; top: 104px; font-family: "PT Sans Narrow", sans-serif; font-weight: 700; font-size: 34px; color: var(--brown); line-height: 1; }
  .millions-note { left: 171px; top: 146px; color: var(--brown); font-size: 18px; line-height: 17px; }
  .people-three { position: absolute; left: 20px; top: 262px; width: 92px; height: 66px; }
  .third { left: 148px; top: 260px; font-size: 72px; }
  .third-note { left: 157px; top: 328px; }
  .tenth { left: 20px; top: 456px; font-size: 72px; }
  .tenth-note { left: 27px; top: 524px; }
  .people-pyramid { position: absolute; left: 246px; top: 424px; width: 130px; height: 140px; }
  .footer { position: absolute; left: 0; top: 1141px; width: 908px; height: 59px; background: var(--footer); }
  .partner { position: absolute; top: 21px; font-weight: 700; font-size: 16px; color: var(--rust-deep); }
  .partner-one { left: 600px; }
  .partner-two { left: 738px; }
</style>
</head>
<body>
<main class="poster">
  <div class="backdrop" role="img" aria-label="Faint illustration of an elder with a feathered headdress behind the poster"></div>

  <div class="title-box"></div>
  <h1 class="title">Bright Trails,<br>Strong Spirits ...</h1>

  <div class="portrait" role="img" aria-label="Photo of a smiling older woman holding a red heart sign"></div>

  <div class="heart">
    <svg viewBox="0 0 292 244" width="292" height="244" aria-hidden="true">
      <path d="M146 244 C 90 190, 0 140, 8 68 C 14 20, 60 0, 96 6 C 122 10, 140 28, 146 44 C 152 28, 170 10, 196 6 C 232 0, 278 20, 284 68 C 292 140, 202 190, 146 244 Z" fill="var(--heart)"/>
    </svg>
    <div class="heart-text">
      <span class="heart-lead">Alzheimer's is the</span>
      <span class="heart-num">6</span>
      <span class="heart-sup">th</span>
      <span class="heart-rest">leading<br>cause<br>of Death</span>
    </div>
  </div>

  <h2 class="subtitle">The River of Life Flows<br>Through the Heart,<br>Protecting the Mind<br>and Body</h2>
  <div class="hatch"></div>

  <p class="risk">Elders with diabetes, heart disease,<br>or high blood pressure have a much<br>higher risk of developing Alzheimer's<br>or other dementias</p>
  <svg class="pulse" viewBox="0 0 370 44" aria-hidden="true">
    <polyline points="0,30 240,30 246,18 252,44 258,8 264,30 300,30 306,22 312,30 350,30 354,20 358,38 362,30 370,30" fill="none" stroke="#fff" stroke-width="1.5"/>
    <circle cx="282" cy="20" r="11" fill="none" stroke="#fff" stroke-width="1.5"/>
    <path d="M330 30 C 318 22, 320 12, 328 14 C 332 15, 334 18, 334 20 C 334 18, 336 15, 340 14 C 348 12, 350 22, 338 30 Z" fill="none" stroke="#fff" stroke-width="1.5"/>
  </svg>

  <div class="cta-label">Make an appointment<br>with your doctor today</div>
  <p class="cta-text">to talk about how to keep<br>your mind and heart healthy.</p>
  <div class="cta-rule"></div>

  <div class="border-band" role="img" aria-label="Woven geometric border pattern"></div>

  <section class="facts">
    <div class="map" role="img" aria-label="Map of the United States"></div>
    <span class="stat-big millions">5.7</span>
    <span class="millions-unit">MILLION</span>
    <p class="stat-note millions-note">Americans have<br>Alzheimer's<br>Disease</p>

    <svg class="people-three" viewBox="0 0 84 66" aria-hidden="true">
      <g fill="var(--brown)"><circle cx="12" cy="6" r="5"/><rect x="5" y="13" width="14" height="26" rx="3"/><rect x="6" y="38" width="5" height="28"/><rect x="13" y="38" width="5" height="28"/></g>
      <g fill="var(--cream)"><circle cx="42" cy="6" r="5"/><path d="M36 13 H48 L54 44 H30 Z"/><rect x="37" y="44" width="4" height="22"/><rect x="43" y="44" width="4" height="22"/></g>
      <g fill="var(--cream)"><circle cx="72" cy="6" r="5"/><rect x="65" y="13" width="14" height="26" rx="3"/><rect x="66" y="38" width="5" height="28"/><rect x="73" y="38" width="5" height="28"/></g>
    </svg>
    <span class="stat-big third">1 in 3</span>
    <p class="stat-note third-note">American Indians<br>over 65 develop<br>dementia, including<br>Alzheimer's</p>

    <span class="stat-big tenth">1 in10</span>
    <p class="stat-note tenth-note">People age 65<br>and older<br>has Alzheimer's</p>
    <svg class="people-pyramid" viewBox="0 0 122 140" aria-hidden="true">
      <defs>
        <g id="figure"><circle cx="8" cy="4" r="4"/><rect x="2" y="9" width="12" height="16" rx="2"/><rect x="3" y="24" width="4" height="14"/><rect x="9" y="24" width="4" height="14"/></g>
      </defs>
      <use href="#figure" x="53" y="0" fill="var(--brown)"/>
      <g fill="var(--cream)">
        <use href="#figure" x="37" y="26"/><use href="#figure" x="69" y="26"/>
        <use href="#figure" x="21" y="52"/><use href="#figure" x="53" y="52"/><use href="#figure" x="85" y="52"/>
        <use href="#figure" x="5" y="78"/><use href="#figure" x="37" y="78"/><use href="#figure" x="69" y="78"/><use href="#figure" x="101" y="78"/>
        <use href="#figure" x="0" y="102"/><use href="#figure" x="53" y="102"/>
      </g>
    </svg>
  </section>

  <footer class="footer">
    <span class="partner partner-one">Kestrel Health</span>
    <span class="partner partner-two">Elder Circle Alliance</span>
  </footer>
</main>
</body>
</html>
```